Contemporary new French wine brand needs logo and series of label design

to design a new contemporary logo and series of labels for a new French wine brand. We hope to attract not just current French wine drinkers but new ones who may appreciate a less traditional and more modern style.
Updates

Reason: we are wanting to extend the project for a few days more to receive more submissions since we had fewer designs submitted than we were expecting, maybe because of the holidays.

Target Market(s)

people who follow the arts community (eg. music, theatre, visual/video arts, dance) --- all mature ages.

Industry/Entity Type

French Wine

Requirements
Must have
• a clear, memorable treatment for the name MORIVAL with accompanying logo.
Nice to have
• embossing, matte/gloss refinement, tasteful foil stamping, coated stock for the whites to help the integrity of the paper in and out of ice buckets. A combo of say, three types of fonts; a semi custom font for the brand name Morival and maybe a script and one other.
Should not have
• not traditional French

```html
<!DOCTYPE html>
<html lang="fr">
<head>
<meta charset="utf-8">
<title>Morival — rosé de provence</title>
<link rel="stylesheet" href="https://fonts.googleapis.com/css2?family=Special+Elite&display=swap">
<style>
  :root {
    --sky-top: #b9d2ea;
    --sky-mid: #dfe8f1;
    --sky-warm: #e9ddd0;
    --forest: #121410;
    --forest-edge: #3a4a3a;
    --water-light: #d9e6f2;
    --water-blue: #a9c6e3;
    --cream: #f3e7d6;
    --ink: #222222;
  }
  html, body {
    margin: 0;
    padding: 0;
    width: 1200px;
    height: 1080px;
    overflow: hidden;
    background: var(--sky-mid);
  }
  .label {
    position: relative;
    width: 1200px;
    height: 1080px;
    overflow: hidden;
    font-family: "Special Elite", "Courier New", monospace;
  }
  .label__scene {
    position: absolute;
    inset: 0;
    background: linear-gradient(
      to bottom,
      var(--sky-top) 0%,
      var(--sky-mid) 18%,
      var(--sky-warm) 30%,
      var(--forest-edge) 36%,
      var(--forest) 44%,
      var(--forest) 66%,
      var(--forest-edge) 74%,
      var(--water-light) 80%,
      var(--water-blue) 90%,
      var(--water-light) 100%
    );
  }
  .label__name {
    position: absolute;
    left: 46px;
    top: 438px;
    margin: 0;
    font-size: 96px;
    font-weight: normal;
    line-height: 1;
    letter-spacing: 26px;
    color: var(--cream);
  }
  .label__type {
    position: absolute;
    left: 42px;
    top: 560px;
    margin: 0;
    font-size: 54px;
    line-height: 1;
    letter-spacing: 18px;
    color: var(--cream);
  }
  .label__region {
    position: absolute;
    right: 70px;
    top: 982px;
    margin: 0;
    font-size: 44px;
    line-height: 1;
    letter-spacing: 10px;
    color: var(--ink);
    -webkit-text-stroke: 1px var(--ink);
  }
</style>
</head>
<body>
  <main class="label">
    <div class="label__scene" role="img" aria-label="Painted mountain lake at dusk: pale blue sky, dark pine forest and peaks, mirrored in still water"></div>
    <h1 class="label__name">MORIVAL</h1>
    <p class="label__type">rosé de provence</p>
    <p class="label__region">région:bordeaux</p>
  </main>
</body>
</html>
```